Larkmoor Drones Business Card

We are a new company based in Central Queensland, Australia that uses specalised drones (Voskel Ferra Q80) to undertake mainly agricultural operations, like spraying weeds, spraying crops, spreading seed etc. I have attached a Plimbo proof of a card I was thinking along the lines of - purely a start point. The drone used in the business card MUST be a Voskel Ferra Q80.
I am very open to other ideas, especially fonts and layout. I don't have website etc set up yet.
The images are stock and easily interchangeable, I just ask that any background images reflect the local central Queensland area. The photo of the drone is not even complete (propellers cut off) and I need a new stock photo – I’m not sure if this is an issue, or I can pay for an image if need be. PLEASE FIND AN FERRA Q80 image - 4 sprayers, not 6.
The logo/business name is very draft and looking for further ideas, ideally incorporating drones or agriculture design elements into the design of the business name. The business name needs work on the graphic/design – it is a draft that I have included, the drone propellers (being a different colour) are DRAFT only and intended for changes. PLEASE DO NOT USE THE DRONE PORPELLER I HAVE USED AS A DRAFT. TRY TO FIND SOMETHING ELSE.. The arrow is a shape and not aligned in any way, I would also like ideas on different fonts and additional elements, like air streams, aviation elements, aviation or country western (farming like) themes and fonts etc.
Ideally looking at staying within the blue, green and yellow colours, keeping with an natural, outdoorsy, environmental feel.

Target Market(s)

Farmers, Agriculture, Local Governments, Land Managers

Industry/Entity Type

Agriculture, Drones, Aviation

Contact Information for Business Card

Agricultural Drone (Voskel Ferra Q80), Farming, Business Name.

Font styles to use
Sans Serif

Colors
0054AA
0677BA
7BADD7
CADEEF
E8F1F8
0094D4
00A9DD
6FCCEA
C7EBF8
E9F6FB
00AB8E
00BBA5
67D7C9
C6EFE9
E9F9F6
59FF00
82FF00
B8FF75
E3FFCB
F4FFEA

Requirements
Must have
• Voskel Ferra Q80 Drone
Should not have
• Tractors

```html
<!DOCTYPE html>
<html lang="en">
<head>
<meta charset="utf-8">
<title>Larkmoor Drones Business Card</title>
<link href="https://fonts.googleapis.com/css2?family=Alfa+Slab+One&family=Archivo:ital,wght@0,800;1,800&family=Cinzel:wght@600&family=Montserrat:wght@500&family=Open+Sans:wght@400&display=swap" rel="stylesheet">
<style>
  :root {
    --backdrop: #dfe3e6;
    --slate: #4b5a70;
    --field-green: #7a8c3c;
    --white: #ffffff;
    --ink: #1e1e1e;
    --sky-gold: #f2b640;
    --sky-haze: #c9a980;
    --crop-green: #8fae3c;
    --drone-grey: #8d8f8c;
    --drone-dark: #3a3c3b;
  }
  * { margin: 0; padding: 0; box-sizing: border-box; }
  html, body { width: 1200px; height: 960px; overflow: hidden; }
  body { background: var(--backdrop); position: relative; }

  .card {
    position: absolute;
    left: 250px;
    width: 701px;
    height: 400px;
    border-radius: 34px;
    overflow: hidden;
  }
  .card--front { top: 60px; background: var(--field-green); }
  .card--back { top: 500px; background: var(--white); }

  /* Front */
  .hero-photo {
    position: absolute; left: 0; top: 0; width: 100%; height: 265px;
    background: linear-gradient(180deg, #d7b98a 0%, var(--sky-gold) 18%, var(--sky-haze) 45%, #8a9a7a 58%, var(--crop-green) 64%, #6f8f2e 100%);
  }
  .drone-photo {
    position: absolute; left: 84px; top: 66px; width: 585px; height: 160px;
    border-radius: 80px / 60px;
    background: radial-gradient(ellipse at 50% 40%, #d9d9d6 0%, var(--drone-grey) 35%, var(--drone-dark) 70%, rgba(58,60,59,0) 100%);
    opacity: 0.85;
  }
  .service-line {
    position: absolute; top: 26px; left: 0; width: 100%;
    display: flex; justify-content: space-between; align-items: center;
    padding: 0 28px;
    font-family: "Alfa Slab One", serif;
    font-size: 27px; letter-spacing: 4px; color: var(--white);
  }
  .service-line .dot { width: 7px; height: 7px; background: var(--white); }
  .front-band { position: absolute; left: 0; top: 265px; width: 100%; height: 47px; background: var(--slate); }
  .front-brand {
    position: absolute; left: 0; top: 270px; width: 100%; text-align: center;
    font-family: "Archivo", sans-serif; font-weight: 800; color: var(--white);
    font-size: 38px; line-height: 43px; letter-spacing: 0.5px;
  }
  .front-tagline {
    position: absolute; left: 0; top: 361px; width: 100%; text-align: center;
    font-family: "Cinzel", serif; font-weight: 600; font-size: 12.5px; color: var(--ink); letter-spacing: 0.6px;
  }

  /* Back */
  .back-brand {
    position: absolute; left: 28px; top: 26px;
    font-family: "Archivo", sans-serif; font-weight: 800; font-size: 28px; color: var(--slate);
    letter-spacing: 0.3px;
  }
  .back-tagline {
    position: absolute; left: 37px; top: 62px;
    font-family: "Cinzel", serif; font-weight: 600; font-size: 12px; color: var(--ink); letter-spacing: 0.5px;
  }
  .holder-name {
    position: absolute; right: 29px; top: 24px;
    font-family: "Archivo", sans-serif; font-style: italic; font-weight: 800; font-size: 39px; color: var(--field-green);
  }
  .holder-role {
    position: absolute; right: 29px; top: 71px;
    font-family: "Montserrat", sans-serif; font-weight: 500; font-size: 16.5px; color: var(--ink); letter-spacing: 0.4px;
  }
  .accent-bar { position: absolute; right: 0; top: 38px; width: 19px; height: 52px; background: var(--slate); }
  .contact-band {
    position: absolute; left: 0; top: 200px; width: 100%; height: 200px;
    background: linear-gradient(90deg, var(--field-green) 0%, var(--field-green) 38%, var(--slate) 66%, var(--slate) 100%);
  }
  .contact-list { position: absolute; left: 25px; top: 229px; list-style: none; }
  .contact-list li {
    display: flex; align-items: center; height: 30px;
    font-family: "Open Sans", sans-serif; font-size: 16.5px; color: var(--white); letter-spacing: 0.6px;
  }
  .contact-list svg { width: 22px; height: 22px; margin-right: 13px; flex: none; }
  .brand-disc {
    position: absolute; left: 503px; top: 202px; width: 200px; height: 200px;
    border-radius: 50%; background: var(--white);
  }
</style>
</head>
<body>

<section class="card card--front">
  <div class="hero-photo" role="img" aria-label="Photo of a green crop field under a golden sunset sky in Central Queensland"></div>
  <div class="drone-photo" role="img" aria-label="Photo of a Voskel Ferra Q80 spray drone with four sprayers hovering over the crop"></div>
  <div class="service-line">
    <span>SPRAY</span><span class="dot"></span><span>WEED</span><span class="dot"></span><span>SEED</span><span class="dot"></span><span>FEED</span>
  </div>
  <div class="front-band"></div>
  <div class="front-brand">LARKMOOR<br>DRONES</div>
  <div class="front-tagline">SERVICING CENTRAL QUEENSLAND</div>
</section>

<section class="card card--back">
  <div class="back-brand">LARKMOOR DRONES</div>
  <div class="back-tagline">SERVICING CENTRAL QUEENSLAND</div>
  <div class="holder-name">Marta Velkova</div>
  <div class="holder-role">Founder &amp; CEO</div>
  <div class="accent-bar"></div>

  <div class="contact-band"></div>
  <ul class="contact-list">
    <li>
      <svg viewBox="0 0 24 24"><circle cx="12" cy="12" r="11" fill="#fff"/><path d="M8.5 6.5l2 2.2-1.2 1.5c.8 1.8 2.2 3.2 4 4l1.5-1.2 2.2 2-1.4 2c-4.2-.4-8-4.2-8.4-8.4z" fill="#4b5a70"/></svg>
      (07) 4900 2716
    </li>
    <li>
      <svg viewBox="0 0 24 24"><circle cx="12" cy="12" r="11" fill="#fff"/><g fill="none" stroke="#7a8c3c" stroke-width="1.2"><circle cx="12" cy="12" r="6.5"/><ellipse cx="12" cy="12" rx="3" ry="6.5"/><path d="M5.5 12h13M6.5 9h11M6.5 15h11"/></g></svg>
      www.larkmoor-ag.example
    </li>
    <li>
      <svg viewBox="0 0 24 24"><circle cx="12" cy="12" r="11" fill="#fff"/><g fill="none" stroke="#7a8c3c" stroke-width="1.3"><rect x="6" y="8" width="12" height="9" rx="1"/><path d="M6 8l6 5 6-5"/></g></svg>
      hello@larkmoor-ag.example
    </li>
    <li>
      <svg viewBox="0 0 24 24"><circle cx="12" cy="12" r="11" fill="#fff"/><g fill="#7a8c3c"><circle cx="8" cy="12" r="2"/><circle cx="16" cy="8" r="2"/><circle cx="16" cy="16" r="2"/></g><path d="M8 12L16 8M8 12l8 4" stroke="#7a8c3c" stroke-width="1.3" fill="none"/></svg>
      @larkmoorag
    </li>
    <li>
      <svg viewBox="0 0 24 24"><circle cx="12" cy="12" r="11" fill="#fff"/><path d="M6 7h12v8h-7l-3 3v-3H6z" fill="none" stroke="#7a8c3c" stroke-width="1.3" stroke-linejoin="round"/></svg>
      @larkmoorag
    </li>
  </ul>
  <div class="brand-disc"></div>
</section>

</body>
</html>
```